Business card design for my company.
I would like the card's background colour to be black. You can also see our web site to get an idea of our brand. https://www.tmwhomecrafting.com.au/
- Name
- Email

```html
<!DOCTYPE html>
<html lang="en">
<head>
<meta charset="utf-8">
<title>TMW Home Crafting — Business Card</title>
<link rel="stylesheet" href="https://fonts.googleapis.com/css2?family=Montserrat:wght@400;700&display=swap">
<style>
  :root {
    --page: #e9e9e7;
    --card: #202020;
    --green: #1e9a48;
    --white: #f5f5f5;
    --muted: #d9d9d9;
  }
  * { box-sizing: border-box; margin: 0; padding: 0; }
  html, body { width: 1200px; height: 912px; overflow: hidden; }
  body {
    background: var(--page);
    font-family: "Montserrat", sans-serif;
    display: flex;
    flex-direction: column;
    align-items: center;
    justify-content: center;
    gap: 68px;
  }
  .card {
    position: relative;
    width: 620px;
    height: 354px;
    background: var(--card);
    border-radius: 16px;
    overflow: hidden;
    box-shadow: 0 10px 26px rgba(0,0,0,.22);
  }
  .brand {
    display: flex;
    align-items: center;
    gap: 12px;
    color: var(--white);
    font-weight: 700;
    letter-spacing: 3px;
    text-transform: uppercase;
  }
  .brand-mark { width: 18px; height: 18px; background: var(--green); flex: none; }
  .card-front .brand {
    position: absolute;
    left: 50%; top: 50%;
    transform: translate(-50%, -50%);
    font-size: 30px;
    white-space: nowrap;
  }
  .card-back .brand {
    position: absolute;
    left: 240px; top: 70px;
    font-size: 24px;
    white-space: nowrap;
  }
  .card-back .brand .brand-mark { width: 15px; height: 15px; }
  .person {
    position: absolute;
    left: 40px; top: 178px;
    width: 232px;
    text-align: right;
  }
  .person-name {
    color: var(--green);
    font-weight: 700;
    font-size: 23px;
    letter-spacing: 1px;
    text-transform: uppercase;
  }
  .person-role { color: var(--white); font-size: 15px; margin-top: 2px; }
  .divider {
    position: absolute;
    left: 290px; top: 160px;
    width: 1px; height: 84px;
    background: var(--green);
  }
  .contact-list {
    position: absolute;
    left: 312px; top: 160px;
    list-style: none;
    display: flex; flex-direction: column; gap: 9px;
  }
  .contact-item {
    display: flex; align-items: center; gap: 10px;
    color: var(--white); font-size: 14px;
  }
  .contact-icon { width: 13px; height: 13px; flex: none; }
  .card-band { position: absolute; left: 0; bottom: 0; width: 620px; height: 354px; pointer-events: none; }
</style>
</head>
<body>
  <section class="card card-front" aria-label="Card front">
    <div class="brand"><span class="brand-mark"></span>TMW Home Crafting</div>
  </section>

  <section class="card card-back" aria-label="Card back">
    <div class="brand"><span class="brand-mark"></span>TMW Home Crafting</div>

    <div class="person">
      <p class="person-name">Dario Whitfield</p>
      <p class="person-role">CEO/Founder</p>
    </div>

    <span class="divider"></span>

    <ul class="contact-list">
      <li class="contact-item">
        <svg class="contact-icon" viewBox="0 0 24 24" aria-hidden="true"><path fill="#1e9a48" d="M6.6 10.8a15.1 15.1 0 0 0 6.6 6.6l2.2-2.2a1 1 0 0 1 1-.25 11.4 11.4 0 0 0 3.6.57 1 1 0 0 1 1 1V20a1 1 0 0 1-1 1A17 17 0 0 1 3 4a1 1 0 0 1 1-1h3.5a1 1 0 0 1 1 1c0 1.25.2 2.45.57 3.57a1 1 0 0 1-.25 1z"/></svg>
        897-555-0142
      </li>
      <li class="contact-item">
        <svg class="contact-icon" viewBox="0 0 24 24" aria-hidden="true"><rect x="2" y="5" width="20" height="14" fill="#1e9a48"/><path d="M2 5l10 8 10-8" fill="none" stroke="#202020" stroke-width="1.8"/></svg>
        info@tmwhomecrafting.com.au
      </li>
      <li class="contact-item">
        <svg class="contact-icon" viewBox="0 0 24 24" aria-hidden="true"><g fill="none" stroke="#1e9a48" stroke-width="2"><circle cx="12" cy="12" r="9.5"/><ellipse cx="12" cy="12" rx="4" ry="9.5"/><path d="M2.5 12h19M4 7h16M4 17h16"/></g></svg>
        www.tmwhomecrafting.com.au
      </li>
    </ul>

    <svg class="card-band" viewBox="0 0 620 354" aria-hidden="true">
      <polygon points="0,354 0,343 424,296 404,354" fill="#1e9a48"/>
      <polygon points="408,354 424,316 620,280 620,354" fill="#f5f5f5"/>
    </svg>
  </section>
</body>
</html>
```